Logo and Card design for KRV Home Solutions LLC

I need an edgier logo and business card designs. Current logo attached. I like the colors below. I would like the logo to incorporate a home in the design.
Title = Principal-Acquisitions
Email:KRVHOMESOLUTIONS@fernmail.example
555-214-0937
facebook
IG
2 sided business card with the front being contact info a slogan about selling a home fast. The back incorporating What we do. Buy houses, land, or commercial property as is. We find solutions to make the process of selling simple and fair.

Target Market(s)

Motivated house sellers.

Industry/Entity Type

Business

Contact Information for Business Card

Who we are: We are a Faith based Real Estate Investment Company. We pay cash for homes in any condition and can close quick. Whatever the reason you need to sell fast, we can help. We believe in creating win-win solutions to help you in your time of need. We care! We can help!

Logo Text

KRV Home Solutions LLC

Font styles to use
Sans Serif

Colors
33a6d7
0355a3
85abd2
cee9f5
9d9d9d
b2b2b2
ffffff

Requirements
Must have
• Old logo attached. I want something edgier.
• Company name, phone number, description on the back of what we can do. Pay all cash. Buy in as is condition. No fees,Commisions or closing costs.Close quick. No hassles with solutions to meet your unique situation.
• Call today for an offer within 24 hours.

```html
<!DOCTYPE html>
<html lang="en">
<head>
<meta charset="utf-8">
<title>KRV Home Solutions – Business Card</title>
<link href="https://fonts.googleapis.com/css2?family=Roboto:wght@400;500;700&family=Roboto+Condensed:wght@400;700&display=swap" rel="stylesheet">
<style>
  :root {
    --backdrop: #2b2b2b;
    --navy: #1d3466;
    --ink: #3a3a3a;
    --white: #ffffff;
    --wash: rgba(245, 247, 238, 0.72);
  }
  * { margin: 0; padding: 0; box-sizing: border-box; }
  html, body { width: 1200px; height: 960px; overflow: hidden; }
  body {
    background: var(--backdrop);
    position: relative;
    font-family: "Roboto", sans-serif;
  }
  .card {
    position: absolute;
    width: 600px;
    height: 342px;
    overflow: hidden;
    box-shadow: 0 4px 10px rgba(0,0,0,0.45);
  }

  /* Front */
  .card--front { left: 314px; top: 114px; background: #eef0e4; }
  .front__photo {
    position: absolute; inset: 0;
    background: linear-gradient(180deg, #d9dcd4 0%, #c7cbbf 35%, #9fb884 62%, #8fb06a 80%, #a7bf86 100%);
  }
  .front__wash { position: absolute; inset: 0; background: var(--wash); }
  .front__band {
    position: absolute; left: 0; top: 0; width: 100%; height: 108px;
    background: var(--navy);
  }
  .front__name {
    position: absolute; left: 33px; top: 33px;
    font-family: "Roboto Condensed", sans-serif;
    font-weight: 700; font-size: 23px; color: var(--white);
    letter-spacing: 0.3px;
  }
  .front__title {
    position: absolute; left: 33px; top: 58px;
    font-family: "Roboto Condensed", sans-serif;
    font-size: 16px; color: var(--white);
  }
  .brand {
    position: absolute; display: flex; align-items: center; gap: 10px;
    font-family: "Roboto", sans-serif; font-weight: 700;
    text-transform: uppercase; line-height: 1.1; white-space: nowrap;
  }
  .brand__mark { flex: none; }
  .front__brand {
    right: 40px; top: 124px;
    color: var(--navy); font-size: 25px;
  }
  .front__brand .brand__mark { width: 18px; height: 18px; background: var(--navy); }
  .perks {
    position: absolute; left: 32px; top: 227px;
    list-style: none;
    font-family: "Roboto Condensed", sans-serif;
    font-size: 14.5px; color: var(--ink); line-height: 18px;
  }
  .perks li { position: relative; padding-left: 14px; }
  .perks li::before {
    content: ""; position: absolute; left: 0; top: 7px;
    width: 5px; height: 5px; border-radius: 50%; background: var(--navy);
  }
  .contact {
    position: absolute; right: 32px; top: 259px;
    list-style: none; text-align: right;
    font-size: 14.5px; color: var(--ink); line-height: 19px;
  }
  .contact li { display: flex; justify-content: flex-end; align-items: center; gap: 6px; }
  .contact svg { width: 13px; height: 13px; fill: var(--navy); flex: none; }

  /* Back */
  .card--back { left: 311px; top: 472px; height: 343px; background: var(--navy); color: var(--white); text-align: center; }
  .back__brand {
    left: 0; right: 0; top: 98px; justify-content: center;
    color: var(--white); font-size: 28px;
  }
  .back__brand .brand__mark { width: 20px; height: 20px; background: var(--white); }
  .back__copy { position: absolute; left: 0; right: 0; top: 169px; font-size: 15px; line-height: 18px; }
  .back__heading { font-weight: 700; font-size: 15px; margin-bottom: 3px; }
  .back__section + .back__section { margin-top: 11px; }
</style>
</head>
<body>

<section class="card card--front" aria-label="Business card front">
  <div class="front__photo" role="img" aria-label="Photo of a suburban house with a green lawn and garden path"></div>
  <div class="front__wash"></div>
  <div class="front__band"></div>
  <h1 class="front__name">JORDAN HALE</h1>
  <p class="front__title">Principal-Acquisitions</p>

  <div class="brand front__brand">
    <span class="brand__mark"></span>
    <span>KRV Home Solutions</span>
  </div>

  <ul class="perks">
    <li>Pay all cash. Buy in as is condition</li>
    <li>No fees,Commisions or closing costs</li>
    <li>Close quick. No hassles with<br>solutions to meet your unique situation</li>
    <li>Call today for an offer within 24 hours</li>
  </ul>

  <ul class="contact">
    <li>555-214-0937
      <svg viewBox="0 0 24 24" aria-hidden="true"><path d="M6.6 10.8a15.5 15.5 0 0 0 6.6 6.6l2.2-2.2c.3-.3.7-.4 1-.2 1.1.4 2.3.6 3.6.6.6 0 1 .4 1 1V20c0 .6-.4 1-1 1A17 17 0 0 1 3 4c0-.6.4-1 1-1h3.5c.6 0 1 .4 1 1 0 1.3.2 2.5.6 3.6.1.3 0 .7-.2 1z"/></svg>
    </li>
    <li>KRVHOMESOLUTIONS@fernmail.example
      <svg viewBox="0 0 24 24" aria-hidden="true"><path d="M2 5h20v14H2z M3 6.2v.6l9 6 9-6v-.6z" fill-rule="evenodd"/></svg>
    </li>
    <li>KRVHOMESOLUTIONS.example
      <svg viewBox="0 0 24 24" aria-hidden="true"><path d="M12 2a10 10 0 1 0 0 20 10 10 0 0 0 0-20zm-1 17.9A8 8 0 0 1 4.1 10l4.9 5v1a2 2 0 0 0 2 2zm6.9-2.5A2 2 0 0 0 16 16h-1v-3a1 1 0 0 0-1-1H8v-2h2a1 1 0 0 0 1-1V7h2a2 2 0 0 0 2-2v-.4a8 8 0 0 1 2.9 12.8z"/></svg>
    </li>
  </ul>
</section>

<section class="card card--back" aria-label="Business card back">
  <div class="brand back__brand">
    <span class="brand__mark"></span>
    <span>KRV Home Solutions</span>
  </div>
  <div class="back__copy">
    <div class="back__section">
      <h2 class="back__heading">WHO WE ARE</h2>
      <p>We are a Faith based Real Estate Investment Company. We pay cash for<br>homes in any condition and can close quick. Whatever the reason you need<br>to sell fast, we can help. We believe in creating win-win solutions to help</p>
    </div>
    <div class="back__section">
      <h2 class="back__heading">WHAT WE DO</h2>
      <p>Buy houses, land, or commercial property as is.<br>We find solutions to make the process of selling simple and fair.</p>
    </div>
  </div>
</section>

</body>
</html>
```